packing for cake and sweet

we need packing design for cake box.
I attached some nice packing from other shop like :
Vira and belmonde for examples.

I attached the logo.
you can make packing with any colors you choose.

box size :
length : 30 cm
Width : 30 cm
Height : 15 cm

this shops have very good design :
https://www.brambleworth.example/hot-chocolate/discover-hot-chocolate/all-hot-chocolate

Industry/Entity Type

food

Font styles to use
Other font styles liked:
• same our logo already attached.

```html
<!DOCTYPE html>
<html lang="en">
<head>
<meta charset="utf-8">
<title>Solenne Cake Box – Packaging Sheet</title>
<link rel="stylesheet" href="https://fonts.googleapis.com/css2?family=Open+Sans:wght@400;500&family=Noto+Sans+Arabic:wght@400&display=swap">
<style>
  :root {
    --paper: #ffffff;
    --ink: #111111;
    --ink-soft: #3a3a3a;
    --box-blue: #e2f2fb;
    --panel-blue: #e1f1fb;
    --label-white: #fbf5f7;
    --brand-lilac: #8e9cc8;
    --floral-pink: #f3c3c4;
    --floral-peach: #f7d9cc;
    --fold-line: #b9c6cf;
    --accent-green: #2bb594;
    --drawing-grey: #f3f4f5;
  }
  * { margin: 0; padding: 0; box-sizing: border-box; }
  html, body { width: 1200px; height: 1200px; overflow: hidden; background: var(--paper); }
  .sheet { position: relative; width: 1200px; height: 1200px; font-family: "Open Sans", sans-serif; color: var(--ink); }

  .print-note {
    position: absolute; left: 265px; top: 131px;
    font-size: 15.5px; line-height: 20px; color: var(--ink);
  }

  .lid-artwork {
    position: absolute; left: 257px; top: 253px; width: 213px; height: 213px;
    background: var(--panel-blue);
  }
  .lid-artwork .floral {
    position: absolute; left: 20px; top: 28px; width: 170px; height: 162px;
    border-radius: 40%;
    background: radial-gradient(circle at 60% 35%, var(--floral-peach) 0%, var(--floral-pink) 45%, rgba(225,241,251,0) 72%);
  }
  .lid-artwork .label {
    position: absolute; left: 53px; top: 61px; width: 103px; height: 103px;
    background: var(--label-white);
    display: flex; align-items: center; justify-content: center;
  }
  .lid-artwork .brand-name {
    font-family: "Open Sans", sans-serif; font-weight: 400;
    font-size: 15px; letter-spacing: 1px; color: var(--brand-lilac);
    text-transform: uppercase;
  }

  .message-ar {
    position: absolute; right: 607px; top: 508px; width: 470px;
    font-family: "Noto Sans Arabic", sans-serif; font-size: 14.5px; line-height: 27px;
    color: var(--ink-soft); direction: rtl; text-align: right;
  }
  .status-dot {
    position: absolute; left: 585px; top: 559px; width: 6px; height: 6px;
    border-radius: 50%; background: var(--accent-green);
  }

  .assembly-views {
    position: absolute; left: 209px; top: 703px; width: 350px; height: 226px;
    background: var(--drawing-grey);
  }

  .box-size {
    position: absolute; left: 250px; top: 933px;
    font-size: 54px; font-weight: 500; letter-spacing: -0.5px; color: var(--ink);
  }

  .dieline { position: absolute; left: 0; top: 0; width: 1200px; height: 1200px; }
  .dieline .panel { fill: var(--box-blue); }
  .dieline .cutout { fill: var(--paper); }
  .dieline .fold { stroke: var(--fold-line); stroke-width: 1; stroke-dasharray: 2 2; fill: none; }
</style>
</head>
<body>
<div class="sheet">

  <p class="print-note">Note: please check with printing press for perfect color code<br>and perfect size, I contact makerloft</p>

  <div class="lid-artwork">
    <div class="floral" role="img" aria-label="Watercolour roses, peonies and dusty-miller leaves framing the label"></div>
    <div class="label"><span class="brand-name">Solenne</span></div>
  </div>

  <p class="message-ar">أخي العزيز تواصلت معهم لمحاولة التواصل معكم. أتمنى من الله ذلك. لا استطيع ارسال ايميلي هنا حتى لا يتم اغلاق صفحتي</p>
  <span class="status-dot"></span>

  <div class="assembly-views" role="img" aria-label="Line drawings of the closed cake box and the open box showing its folding flaps"></div>

  <p class="box-size">30x30x15cm</p>

  <svg class="dieline" viewBox="0 0 1920 1920" aria-label="Flat dieline of the cake box">
    <path class="panel" d="M1150,612 V593 Q1150,575 1168,575 H1461 Q1479,575 1479,593 V612 Z"/>
    <rect class="panel" x="1150" y="612" width="328" height="983"/>
    <path class="panel" d="M1150,612 L1035,758 Q1020,777 1035,796 L1150,940 Z"/>
    <path class="panel" d="M1478,612 L1593,758 Q1608,777 1593,796 L1478,940 Z"/>
    <path class="panel" d="M1150,940 H1003 V1020 A33,33 0 0 0 1068,1022 L1150,1102 Z"/>
    <path class="panel" d="M1478,940 H1626 V1020 A33,33 0 0 1 1561,1022 L1478,1102 Z"/>
    <rect class="panel" x="986" y="1102" width="164" height="328"/>
    <rect class="panel" x="1478" y="1102" width="165" height="328"/>
    <path class="panel" d="M1150,1430 L1068,1512 A33,33 0 0 0 1003,1512 V1595 H1150 Z"/>
    <path class="panel" d="M1478,1430 L1561,1512 A33,33 0 0 1 1626,1512 V1595 H1478 Z"/>
    <path class="cutout" d="M1293,1595 A20,20 0 0 1 1333,1595 Z"/>
    <line class="fold" x1="1150" y1="612" x2="1150" y2="1595"/>
    <line class="fold" x1="1478" y1="612" x2="1478" y2="1595"/>
    <line class="fold" x1="1150" y1="612" x2="1478" y2="612"/>
    <line class="fold" x1="1150" y1="1102" x2="1478" y2="1102"/>
    <line class="fold" x1="1150" y1="1430" x2="1478" y2="1430"/>
    <line class="fold" x1="1150" y1="1595" x2="1478" y2="1595"/>
  </svg>

</div>
</body>
</html>
```